first fantastic look and impression

We are looking for a concept for letterhead, business card, emailfooter and template for invoices or offers for our company in the consultation business.
The dancer is a symbol who we are: it looks simple, but there is a lot of hard work and many years of training in this movement. The look is also what we want: elegant, modern, strong, with a touch of extravaganza
Target Market(s)
Hotelbusiness , Consulting
Font styles to use
Sans Serif
Other font styles liked:
- please give us a option we are open
Requirements
Must have
- We are not typical consultants but sparring partners and coaches for the hotel and that should also be expressed in the design. Maybe there is an icon that supports the whole thing. We are more modern and bolder than our industry colleagues.
we are modern, fresh, agile, fast
Nice to have
- a icon

```html
<!DOCTYPE html>
<html lang="en">
<head>
<meta charset="utf-8">
<title>Halvorsen+Kreis – Envelope</title>
<link rel="stylesheet" href="https://fonts.googleapis.com/css2?family=Roboto:wght@400;500&display=swap">
<style>
  :root {
    --backdrop: #e8e8e9;
    --paper: #f4f4f4;
    --ink: #22252e;
    --ink-soft: #4a4c52;
    --seal: #e9e9e9;
  }
  * { margin: 0; padding: 0; box-sizing: border-box; }
  html, body { width: 1200px; height: 795px; overflow: hidden; }
  body {
    background: var(--backdrop);
    font-family: "Roboto", Arial, sans-serif;
    position: relative;
  }
  .envelope {
    position: absolute;
    width: 540px;
    height: 270px;
    background: var(--paper);
    box-shadow: 0 1px 3px rgba(0,0,0,0.08);
  }
  .envelope--back { left: 610px; top: 70px; }
  .envelope--front { left: 50px; top: 440px; }

  .envelope__flap { position: absolute; inset: 0; width: 100%; height: 100%; }

  .wordmark {
    position: absolute;
    left: 66px;
    top: 44px;
    color: var(--ink);
    font-weight: 500;
    font-size: 19px;
    letter-spacing: 0.22em;
    text-transform: uppercase;
  }
  .contact {
    position: absolute;
    left: 40px;
    top: 108px;
    list-style: none;
  }
  .contact__item {
    display: flex;
    align-items: center;
    gap: 6px;
    color: var(--ink-soft);
    font-size: 12.5px;
    line-height: 17px;
  }
  .contact__icon { width: 11px; height: 11px; flex: none; }
</style>
</head>
<body>

  <section class="envelope envelope--back" aria-label="Envelope back with closing flap">
    <svg class="envelope__flap" viewBox="0 0 540 270" aria-hidden="true">
      <path d="M0 0 H540 V98 Q540 108 530 108 Q420 108 300 100 Q200 94 120 80 Q40 66 10 60 Q0 58 0 48 Z" fill="var(--ink)"/>
      <circle cx="275" cy="98" r="24" fill="var(--seal)"/>
    </svg>
  </section>

  <section class="envelope envelope--front" aria-label="Envelope front">
    <div class="wordmark">Halvorsen+Kreis</div>
    <ul class="contact">
      <li class="contact__item">
        <svg class="contact__icon" viewBox="0 0 12 12" aria-hidden="true"><circle cx="6" cy="6" r="6" fill="var(--ink)"/><path d="M6 2.6a2.1 2.1 0 0 0-2.1 2.1C3.9 6.3 6 9.2 6 9.2s2.1-2.9 2.1-4.5A2.1 2.1 0 0 0 6 2.6z" fill="var(--paper)"/><circle cx="6" cy="4.7" r="0.8" fill="var(--ink)"/></svg>
        4820 Lindau / Brunnweg 14
      </li>
      <li class="contact__item">
        <svg class="contact__icon" viewBox="0 0 12 12" aria-hidden="true"><circle cx="6" cy="6" r="6" fill="var(--ink)"/><path d="M3.6 3.2l1.2-.3.7 1.5-.8.6a4 4 0 0 0 1.9 1.9l.6-.8 1.5.7-.3 1.2c-2.6.2-5-2.2-4.8-4.8z" fill="var(--paper)"/></svg>
        +43 5500 41827
      </li>
      <li class="contact__item">
        <svg class="contact__icon" viewBox="0 0 12 12" aria-hidden="true"><circle cx="6" cy="6" r="6" fill="var(--ink)"/><rect x="3" y="3.8" width="6" height="4.4" rx="0.4" fill="var(--paper)"/><path d="M3.2 4l2.8 2.2L8.8 4" stroke="var(--ink)" stroke-width="0.6" fill="none"/></svg>
        mk@halvorsenkreis.com
      </li>
      <li class="contact__item">
        <svg class="contact__icon" viewBox="0 0 12 12" aria-hidden="true"><circle cx="6" cy="6" r="6" fill="var(--ink)"/><circle cx="6" cy="6" r="3" fill="none" stroke="var(--paper)" stroke-width="0.8"/><path d="M3 6h6M6 3c1.4 1.6 1.4 4.4 0 6M6 3c-1.4 1.6-1.4 4.4 0 6" stroke="var(--paper)" stroke-width="0.6" fill="none"/></svg>
        halvorsenkreis.com
      </li>
    </ul>
  </section>

</body>
</html>
```